Automotive Business Card Design

I would just like a automotive themed card. nothing too extravagant, but catchy.

needs to say something about doing roadside assistance,mobile repairs, Diesel repairs, and Fleet maintenance

it can be single sided or double sided. no preference there.

Industry/Entity Type

Automotive

Contact Information for Business Card

Dean Marlowe
phone 534 861 2093
Name: Brightpath Automotive & Diesel Repair

```html
<!DOCTYPE html>
<html lang="en">
<head>
<meta charset="utf-8">
<title>Brightpath Automotive &amp; Diesel Repair – Business Card</title>
<link href="https://fonts.googleapis.com/css2?family=Lato:wght@300;400;700;900&display=swap" rel="stylesheet">
<style>
  :root {
    --page-bg: #e4e1dc;
    --card-bg: #ffffff;
    --ink: #111111;
    --tile-border: #ffffff;
    --card-shadow: rgba(0,0,0,0.18);
  }
  html, body {
    margin: 0;
    padding: 0;
    width: 1200px;
    height: 1037px;
    overflow: hidden;
    background: var(--page-bg);
    font-family: "Lato", Arial, sans-serif;
    color: var(--ink);
  }
  .sheet {
    position: relative;
    width: 1200px;
    height: 1037px;
  }
  .card {
    position: absolute;
    left: 250px;
    width: 700px;
    height: 420px;
    background: var(--card-bg);
    box-shadow: 0 6px 18px var(--card-shadow);
  }
  .card--info { top: 70px; }
  .card--brand { top: 547px; }

  /* Info side */
  .contact {
    text-align: center;
    padding-top: 60px;
  }
  .contact__name {
    font-size: 30px;
    letter-spacing: 1px;
    line-height: 1;
  }
  .contact__first { font-weight: 900; }
  .contact__last { font-weight: 400; }
  .contact__phone {
    font-size: 18px;
    letter-spacing: 2px;
    margin-top: 4px;
  }
  .services {
    text-align: center;
    margin-top: 34px;
  }
  .services__title {
    font-size: 38px;
    font-weight: 400;
    letter-spacing: 1px;
    margin: 0 0 10px;
  }
  .services__list {
    list-style: none;
    margin: 0;
    padding: 0;
    font-size: 25px;
    font-weight: 400;
    line-height: 1.12;
  }

  /* Brand side */
  .brand-title {
    position: absolute;
    top: 20px;
    left: 0;
    right: 0;
    text-align: center;
    font-weight: 900;
    font-size: 26px;
    letter-spacing: 0.5px;
    text-transform: uppercase;
    margin: 0;
  }
  .collage {
    position: absolute;
    left: 40px;
    top: 66px;
    width: 620px;
    height: 322px;
  }
  .collage__tile {
    stroke: var(--tile-border);
    stroke-width: 3;
  }
</style>
</head>
<body>
<div class="sheet">

  <section class="card card--info">
    <div class="contact">
      <div class="contact__name"><span class="contact__first">Dean</span> <span class="contact__last">Marlowe</span></div>
      <div class="contact__phone">534 861 2093</div>
    </div>
    <div class="services">
      <h2 class="services__title">SERVICES</h2>
      <ul class="services__list">
        <li>Roadside assistance</li>
        <li>Mobile repairs</li>
        <li>Diesel repairs</li>
        <li>And Fleet maintenance</li>
      </ul>
    </div>
  </section>

  <section class="card card--brand">
    <h1 class="brand-title">Brightpath Automotive &amp; Diesel Repair</h1>
    <svg class="collage" viewBox="0 0 620 322" width="620" height="322">
      <defs>
        <linearGradient id="g-phone" x1="0" y1="0" x2="1" y2="1">
          <stop offset="0" stop-color="#f2f3f4"/><stop offset="0.5" stop-color="#9fd06a"/><stop offset="1" stop-color="#3a3d42"/>
        </linearGradient>
        <radialGradient id="g-engine" cx="0.55" cy="0.45" r="0.7">
          <stop offset="0" stop-color="#9aa0a8"/><stop offset="0.45" stop-color="#4b5058"/><stop offset="1" stop-color="#0b0b0c"/>
        </radialGradient>
        <radialGradient id="g-hands" cx="0.35" cy="0.35" r="0.8">
          <stop offset="0" stop-color="#e0b9a0"/><stop offset="0.35" stop-color="#a08a78"/><stop offset="0.75" stop-color="#5d5550"/><stop offset="1" stop-color="#2e2b29"/>
        </radialGradient>
        <linearGradient id="g-tyre" x1="0" y1="0" x2="1" y2="1">
          <stop offset="0" stop-color="#f07a2a"/><stop offset="0.3" stop-color="#2c3a5c"/><stop offset="0.65" stop-color="#26262a"/><stop offset="1" stop-color="#a9acb2"/>
        </linearGradient>
        <linearGradient id="g-mechanic" x1="0" y1="0" x2="1" y2="1">
          <stop offset="0" stop-color="#d97a3e"/><stop offset="0.35" stop-color="#3c6fa8"/><stop offset="0.7" stop-color="#3a3a3c"/><stop offset="1" stop-color="#121212"/>
        </linearGradient>
        <linearGradient id="g-board" x1="0" y1="0" x2="1" y2="1">
          <stop offset="0" stop-color="#efe7e2"/><stop offset="0.4" stop-color="#d8b8a8"/><stop offset="0.7" stop-color="#3f4d72"/><stop offset="1" stop-color="#8a8d96"/>
        </linearGradient>
        <linearGradient id="g-cars" x1="0" y1="0" x2="1" y2="0">
          <stop offset="0" stop-color="#c92c2c"/><stop offset="0.28" stop-color="#d6d7da"/><stop offset="0.6" stop-color="#fbfbfc"/><stop offset="1" stop-color="#cfd2d6"/>
        </linearGradient>
      </defs>
      <rect class="collage__tile" role="img" aria-label="Cartoon smartphone holding repair tools" x="90" y="0" width="80" height="70" fill="url(#g-phone)"/>
      <rect class="collage__tile" role="img" aria-label="Photo of a car engine block on black" x="0" y="70" width="170" height="180" fill="url(#g-engine)"/>
      <rect class="collage__tile" role="img" aria-label="Photo of hands working on an engine" x="170" y="0" width="150" height="200" fill="url(#g-hands)"/>
      <rect class="collage__tile" role="img" aria-label="Photo of a roadside worker changing a tyre" x="320" y="0" width="150" height="200" fill="url(#g-tyre)"/>
      <rect class="collage__tile" role="img" aria-label="Photo of hands repairing a phone circuit board" x="220" y="200" width="250" height="122" fill="url(#g-board)"/>
      <rect class="collage__tile" role="img" aria-label="Photo of a mechanic with a wrench under the bonnet" x="470" y="30" width="150" height="190" fill="url(#g-mechanic)"/>
      <rect class="collage__tile" role="img" aria-label="Photo of a red car and a white hatchback" x="470" y="220" width="150" height="102" fill="url(#g-cars)"/>
    </svg>
  </section>

</div>
</body>
</html>
```